Business Card Design

Business Card for professional consulting firm working with large financial institutions.

Target Market(s)

Executive buyers

Industry/Entity Type

Banking

Contact Information for Business Card

Mild creativity wanted. Not boring, but do elaborate artwork.

Font styles to use
Serif
Sans Serif

Colors

Designer to choose colors to be used in the design.

Requirements
Must have
• Standard business card features - company name, individual name, telephone, website, email, locations.
Nice to have
• Two colors
Should not have
• too many colors, fancy printing, cartoons.

```html
<!DOCTYPE html>
<html lang="en">
<head>
<meta charset="utf-8">
<title>Northvale Partners business card</title>
<link href="https://fonts.googleapis.com/css2?family=Tinos:wght@400;700&display=swap" rel="stylesheet">
<style>
  :root {
    --page-bg: #d9d6d2;
    --card-black: #0b0b0b;
    --card-white: #f7f7f7;
    --swoosh-grey: #b9b9b9;
    --ink-dark: #1c1c1c;
    --ink-light: #e8e8e8;
    --ink-muted: #c9c9c9;
  }
  html, body {
    margin: 0;
    padding: 0;
    width: 1200px;
    height: 886px;
    overflow: hidden;
    background: var(--page-bg);
    font-family: "Tinos", "Times New Roman", serif;
  }
  .canvas {
    position: relative;
    width: 1200px;
    height: 886px;
  }
  .card {
    position: absolute;
    width: 520px;
    height: 297px;
    border-radius: 18px;
    overflow: hidden;
    box-shadow: 0 10px 30px rgba(0,0,0,0.25);
  }
  .card-back {
    left: 70px;
    top: 110px;
    background: linear-gradient(135deg, #1a1a1a 0%, var(--card-black) 55%, #202020 100%);
    display: flex;
    align-items: center;
    justify-content: center;
  }
  .card-back .brand-name {
    color: var(--ink-light);
    font-size: 38px;
  }
  .card-front {
    left: 610px;
    top: 470px;
    background: var(--card-black);
  }
  .card-front .wave {
    position: absolute;
    inset: 0;
  }
  .card-front .brand-name {
    position: absolute;
    left: 70px;
    top: 48px;
    color: var(--ink-dark);
    font-size: 30px;
  }
  .contact-block {
    position: absolute;
    right: 26px;
    top: 150px;
    text-align: right;
    color: var(--ink-muted);
    line-height: 1.15;
  }
  .person-name {
    color: var(--ink-light);
    font-weight: 700;
    font-size: 21px;
  }
  .person-title {
    font-size: 15px;
    margin-bottom: 5px;
  }
  .address-line {
    font-size: 13px;
  }
  .contact-line {
    font-size: 13px;
    display: flex;
    align-items: center;
    justify-content: flex-end;
    gap: 8px;
    margin-top: 2px;
  }
  .contact-line.first { margin-top: 5px; }
  .contact-line svg {
    width: 12px;
    height: 12px;
    fill: var(--ink-light);
  }
</style>
</head>
<body>
<main class="canvas">

  <section class="card card-back" aria-label="Card back">
    <span class="brand-name">Northvale Partners</span>
  </section>

  <section class="card card-front" aria-label="Card front">
    <svg class="wave" viewBox="0 0 520 297" preserveAspectRatio="none" aria-hidden="true">
      <path d="M0,0 H520 V128 C420,136 300,160 210,215 C150,255 70,250 0,215 Z" fill="#b9b9b9"/>
      <path d="M0,0 H520 V118 C420,126 300,150 210,205 C150,245 70,240 0,205 Z" fill="#f7f7f7"/>
    </svg>

    <span class="brand-name">Northvale Partners</span>

    <div class="contact-block">
      <div class="person-name">Daniel Carver</div>
      <div class="person-title">Managing Director</div>
      <div class="address-line">2140 Harbor View Road</div>
      <div class="address-line">Juneau, Alaska 99801</div>
      <div class="contact-line first">907 555 0182
        <svg viewBox="0 0 24 24" aria-label="Phone"><path d="M6.6 10.8a15 15 0 0 0 6.6 6.6l2.2-2.2a1 1 0 0 1 1-.25 11.4 11.4 0 0 0 3.6.6 1 1 0 0 1 1 1V20a1 1 0 0 1-1 1A17 17 0 0 1 3 4a1 1 0 0 1 1-1h3.5a1 1 0 0 1 1 1c0 1.25.2 2.45.6 3.6a1 1 0 0 1-.25 1z"/></svg>
      </div>
      <div class="contact-line">hello@northvalepartners.com
        <svg viewBox="0 0 24 24" aria-label="Email"><path d="M2 5h20v14H2z M4 7v.5l8 5 8-5V7l-8 5z" fill-rule="evenodd"/></svg>
      </div>
      <div class="contact-line">www.northvalepartners.com
        <svg viewBox="0 0 24 24" aria-label="Website"><circle cx="12" cy="12" r="10"/></svg>
      </div>
    </div>
  </section>

</main>
</body>
</html>
```